Public Adjusters Collective Business card

We need to get business card Design for our Company we are Public Adjusters in Chicago Illinois - i like to see good combination and elements from my Company Logo. as well To be an two side design
Updates

Target Market(s)

Home /Business owner Property Managers

Industry/Entity Type

Business

Contact Information for Business Card

to show the Element of our logo i will Like 3D

Font styles to use
Sans Serif

Requirements
Must have
• Logo and Element of the Logo in 3D
Nice to have
• Logo That we Provide 3D Same Colors or open for suggestions
Should not have
• unleare view -

```html
<!DOCTYPE html>
<html lang="en">
<head>
<meta charset="utf-8">
<title>Public Adjusters Collective – Business Card</title>
<link rel="stylesheet" href="https://fonts.googleapis.com/css2?family=Roboto:wght@400;500&display=swap">
<style>
  :root {
    --backdrop: #4a4a4a;
    --paper: #ffffff;
    --navy-deep: #0c1a6e;
    --brand-blue: #1f3fb0;
    --accent-orange: #e0583a;
    --ink-light: #ffffff;
  }
  * { box-sizing: border-box; margin: 0; padding: 0; }
  html, body {
    width: 1105px; height: 1200px; overflow: hidden;
    background: var(--backdrop);
    font-family: "Roboto", Arial, sans-serif;
  }
  .card {
    position: absolute; left: 196px; width: 721px; height: 413px;
    overflow: hidden;
  }
  .card--front { top: 145px; background: var(--paper); }
  .card--back { top: 602px; background: var(--accent-orange); }

  .front-wave { position: absolute; inset: 0; width: 100%; height: 100%; }

  .brand-name {
    position: absolute; left: 36px; top: 186px;
    display: flex; align-items: center; gap: 10px; white-space: nowrap;
    color: var(--brand-blue); font-weight: 500; font-size: 20px; line-height: 1.2;
  }
  .brand-dot {
    flex: none; width: 30px; height: 30px; border-radius: 50%;
    background: var(--brand-blue);
  }

  .contact {
    position: absolute; right: 39px; top: 118px;
    color: var(--ink-light); text-align: right;
  }
  .contact__name { font-size: 23px; font-weight: 500; line-height: 30px; }
  .contact__title { font-size: 19px; line-height: 26px; margin-bottom: 18px; }
  .contact__address { font-size: 17px; line-height: 25px; margin-bottom: 10px; }
  .contact__list { list-style: none; }
  .contact__item {
    display: flex; justify-content: flex-end; align-items: center; gap: 12px;
    font-size: 17px; line-height: 27.5px;
  }
  .contact__icon { width: 18px; height: 18px; fill: var(--ink-light); }

  .back-brand {
    position: absolute; left: 0; right: 0; top: 176px;
    display: flex; justify-content: center; align-items: center; gap: 14px;
    color: var(--ink-light); font-weight: 500; font-size: 28px; white-space: nowrap;
  }
  .back-brand .brand-dot { background: var(--ink-light); width: 38px; height: 38px; }
  .back-url {
    position: absolute; left: 0; right: 0; top: 347px; text-align: center;
    color: var(--ink-light); font-size: 16px; letter-spacing: 2.5px;
  }
</style>
</head>
<body>
  <section class="card card--front">
    <svg class="front-wave" viewBox="0 0 721 413" preserveAspectRatio="none" aria-hidden="true">
      <defs>
        <radialGradient id="navyGlow" cx="75%" cy="45%" r="70%">
          <stop offset="0" stop-color="#2a45d0"/>
          <stop offset="0.6" stop-color="#14259a"/>
          <stop offset="1" stop-color="#0a1460"/>
        </radialGradient>
      </defs>
      <path d="M482 0 H721 V413 H205 C340 330 470 200 482 0 Z" fill="url(#navyGlow)"/>
      <path d="M500 0 C490 190 370 330 190 413" fill="none" stroke="#ffffff" stroke-width="2.5"/>
    </svg>

    <div class="brand-name">
      <span class="brand-dot"></span>
      <span>Public Adjusters Collective</span>
    </div>

    <div class="contact">
      <p class="contact__name">Mara Lindqvist</p>
      <p class="contact__title">President</p>
      <p class="contact__address">2716 Harlow Avenue<br>Oak Lane, IL 60614</p>
      <ul class="contact__list">
        <li class="contact__item">312 555 0148
          <svg class="contact__icon" viewBox="0 0 24 24"><path d="M3 8c0-3 4-4 9-4s9 1 9 4v2h-5V8H8v2H3V8zm4 4h10l3 8H4l3-8zm5 2a2.5 2.5 0 100 5 2.5 2.5 0 000-5z"/></svg></li>
        <li class="contact__item">312 555 0193
          <svg class="contact__icon" viewBox="0 0 24 24"><path d="M7 1h10a2 2 0 012 2v18a2 2 0 01-2 2H7a2 2 0 01-2-2V3a2 2 0 012-2zm0 3v14h10V4H7zm5 15.5a1 1 0 100 2 1 1 0 000-2z"/></svg></li>
        <li class="contact__item">312 555 0176
          <svg class="contact__icon" viewBox="0 0 24 24"><path d="M6 2h12v6H6V2zm-3 8h18v8h-3v4H6v-4H3v-8zm5 5v5h8v-5H8z"/></svg></li>
        <li class="contact__item">mara@qpac.com
          <svg class="contact__icon" viewBox="0 0 24 24"><path d="M2 5h20v14H2V5zm2 2v.5l8 5 8-5V7H4z"/></svg></li>
        <li class="contact__item">www.qpac.com
          <svg class="contact__icon" viewBox="0 0 24 24"><path d="M12 2a10 10 0 110 20 10 10 0 010-20zm-1 4c-2 1-3 3-2 4s3 0 3 2-2 3-1 5c2 0 5-1 6-4-1-1-3 0-3-2 0-1 2-1 2-3-1-1-3-2-5-2z"/></svg></li>
      </ul>
    </div>
  </section>

  <section class="card card--back">
    <div class="back-brand">
      <span class="brand-dot"></span>
      <span>Public Adjusters Collective</span>
    </div>
    <p class="back-url">www.PublicAdjustersCollective.com</p>
  </section>
</body>
</html>
```